Brightfen Business Card Redesign & Logo Update

We need to update our business cards to something more modern and fresh. Brightfen can provide the current color schemes and old design examples, but welcome creativity in helping us with this redesign. PLEASE NOTE that we no longer utilize the "tree" and/or "leaf" imagery in our branding. If able would apprecaite an update on the quality of our "words only" logo in Ai. / PNG formats too.

Target Market(s)

Investors, landowners, corporate partners, contractors

Industry/Entity Type

Environmental Restoration & Conservation

Contact Information for Business Card

Logo, persons name, title, mailing address, phone and email, website url

Font styles to use
Other font styles liked:
• Merriweather

Requirements
Nice to have
• Logo, persons name, title, mailing address, phone and email, website url, but open to ideams
Should not have
• No all back backgrounds

```html
<!DOCTYPE html>
<html lang="en">
<head>
<meta charset="UTF-8">
<title>Brightfen Business Card</title>
<link href="https://fonts.googleapis.com/css2?family=Merriweather:wght@400;700;900&display=swap" rel="stylesheet">
<style>
  :root {
    --stage: #d4d4d4;
    --card: #ffffff;
    --ink: #2b2b2b;
    --ink-soft: #4a4a4a;
    --orange: #ee7d1f;
    --green: #1e8a3c;
    --card-shadow: 0 10px 24px rgba(0,0,0,0.18);
  }
  * { box-sizing: border-box; margin: 0; padding: 0; }
  html, body { width: 1200px; height: 781px; overflow: hidden; }
  body {
    background: radial-gradient(ellipse at 50% 45%, #e2e2e2 0%, var(--stage) 100%);
    font-family: "Merriweather", Georgia, serif;
    color: var(--ink);
    position: relative;
  }
  .card {
    position: absolute;
    background: var(--card);
    border-radius: 22px;
    box-shadow: var(--card-shadow);
  }
  /* Back: vertical contact side */
  .card-back {
    left: 150px; top: 120px;
    width: 300px; height: 525px;
    padding: 40px 34px;
  }
  .brand-name {
    font-weight: 900;
    color: var(--green);
    letter-spacing: 0.5px;
    line-height: 1;
  }
  .card-back .brand-name { font-size: 38px; }
  .social-list {
    display: flex; gap: 10px;
    margin-top: 34px;
  }
  .social-dot {
    width: 22px; height: 22px; border-radius: 50%;
    background: var(--green);
  }
  .social-dot.accent { background: var(--orange); }
  .contact-block {
    position: absolute;
    left: 34px; right: 24px; bottom: 40px;
  }
  .person-name {
    font-weight: 700; font-size: 19px; letter-spacing: 1px;
    color: var(--ink);
  }
  .person-title {
    font-size: 12px; color: var(--orange);
    margin-top: 4px;
  }
  .address {
    font-size: 12px; line-height: 1.6; color: var(--ink-soft);
    margin-top: 12px;
  }
  .contact-lines { list-style: none; margin-top: 12px; }
  .contact-lines li {
    display: flex; align-items: center; gap: 8px;
    font-size: 12px; line-height: 1.9; color: var(--ink-soft);
  }
  .contact-lines svg { width: 12px; height: 12px; flex: none; }
  /* Front: horizontal logo side */
  .card-front {
    left: 540px; top: 170px;
    width: 520px; height: 300px;
    display: flex; align-items: center; justify-content: center;
  }
  .card-front .brand-name { font-size: 64px; }
</style>
</head>
<body>
  <section class="card card-back" aria-label="Business card, contact side">
    <div class="brand-name">Brightfen</div>
    <div class="social-list" aria-label="Social links">
      <span class="social-dot"></span>
      <span class="social-dot accent"></span>
      <span class="social-dot"></span>
    </div>
    <div class="contact-block">
      <div class="person-name">DANA REYES</div>
      <div class="person-title">Director</div>
      <div class="address">4810 Meadow Lane 27,<br>Marlow, TX 75110</div>
      <ul class="contact-lines">
        <li>
          <svg viewBox="0 0 12 12"><path d="M2.5 1h2l1 3-1.3 1a6 6 0 0 0 2.8 2.8L8 6.5l3 1v2A1.5 1.5 0 0 1 9.5 11 8.5 8.5 0 0 1 1 2.5 1.5 1.5 0 0 1 2.5 1z" fill="#1e8a3c"/></svg>
          (555) 014-2287
        </li>
        <li>
          <svg viewBox="0 0 12 12"><rect x="0.5" y="2" width="11" height="8" rx="1" fill="#1e8a3c"/><path d="M1 2.5l5 4 5-4" stroke="#fff" stroke-width="1" fill="none"/></svg>
          info@brightfencredits.com
        </li>
        <li>
          <svg viewBox="0 0 12 12"><circle cx="6" cy="6" r="5" fill="none" stroke="#1e8a3c" stroke-width="1.3"/><path d="M1 6h10M6 1c-2.5 3-2.5 7 0 10M6 1c2.5 3 2.5 7 0 10" stroke="#1e8a3c" stroke-width="1" fill="none"/></svg>
          www.brightfencredits.com
        </li>
      </ul>
    </div>
  </section>

  <section class="card card-front" aria-label="Business card, logo side">
    <div class="brand-name">Brightfen</div>
  </section>
</body>
</html>
```